Lantern Petals Website v.1 - attract floral shop franchisees

I need a simple information website for my new business. We are a franchisor of flower shops. The overall purpose of the website is to promote the company and the service, especially to potential franchisees and retailers. Only about 4 pages are required including homepage, About, For Supermarkets, For Franchisees, and Contact. No special functions are required except the site will have two separate inquiry forms that must be filled out online and submitted via automated email. Similarly, an email form should be linked from the Contact page. I have a logo and business cards designed by ArtMingle, and I would like the site to have a consistent color scheme and style. The key to design will be to express the joy and love associated with flowers and floral bouquets.
IMPORTANT - I will be exporting the website design to Wordpress CMS in a site hosted by HostNimbus. For smooth integration into WordPress hosted by HostNimbus, the designer should build the site using a WordPress-friendly format. Ideally, they should use HTML, CSS, and PHP. Creating a custom theme or using a page builder that exports to WordPress-compatible files is best. This ensures the site can be easily imported and managed within WordPress.

Target Market(s)

Potential franchisees (existing florists or creative types who might like to own a floral business) and supermarkets who might want us to run their floral department

Industry/Entity Type

Floral retailing

Requirements
Must have
• A brand theme that is beautiful, consistent throughout and builds on the logo design
Nice to have
• Show gender and ethnic diversity in customers and florists. Pictures of happy florists (for franchisees) and pictures of amazing floral department displays (for supermarkets)

```html
<!DOCTYPE html>
<html lang="en">
<head>
<meta charset="UTF-8">
<title>Lantern Petals – Flower Shop Franchising</title>
<link href="https://fonts.googleapis.com/css2?family=Montserrat:wght@400;500;600;700;800&family=Great+Vibes&display=swap" rel="stylesheet">
<style>
:root{
  --orange:#f39a1b;
  --orange-dark:#e4850a;
  --green:#1f9a3f;
  --ink:#1b1b1b;
  --text:#3a3a3a;
  --muted:#8a8a8a;
  --cream:#fdf7e8;
  --lilac:#f3f3f8;
  --mint:#edf6f0;
  --line:#dcdcdc;
  --black:#111111;
  --white:#ffffff;
}
*{box-sizing:border-box;margin:0;padding:0}
html,body{width:1200px;height:4521px;overflow:hidden}
body{position:relative;background:var(--white);font-family:'Montserrat',sans-serif;color:var(--text)}
.abs{position:absolute}
.script{font-family:'Great Vibes',cursive;font-weight:400;color:var(--ink)}

/* header */
.brand{position:absolute;display:flex;align-items:center;gap:12px}
.brand-dot{width:46px;height:46px;border-radius:50%;background:var(--orange)}
.brand-name{font-size:30px;font-weight:700;color:var(--orange);letter-spacing:.5px}
.nav{position:absolute;top:58px;left:614px;display:flex;gap:38px;font-size:13px;font-weight:500;color:var(--ink)}
.nav .active{color:var(--orange);border-bottom:1px solid var(--orange);padding-bottom:3px}

/* buttons */
.btn{position:absolute;height:34px;border-radius:17px;background:var(--orange);color:#fff;font-size:11.5px;font-weight:600;display:flex;align-items:center;padding-left:16px;width:142px}
.btn::after{content:"";position:absolute;right:4px;top:4px;width:26px;height:26px;border-radius:50%;background:#fff;box-shadow:inset 0 0 0 7px #fff,inset 0 0 0 13px var(--orange)}

/* photo placeholders */
.photo{position:absolute;overflow:hidden}
.bloom{position:absolute;border-radius:50%}

/* section headings */
.sec-title{position:absolute;display:flex;align-items:baseline;gap:6px;font-weight:700;font-size:35px;color:var(--ink);white-space:nowrap}
.sec-title .script{font-size:64px;line-height:1}

/* hero */
.hero-title{left:140px;top:250px;font-size:37px;font-weight:700;line-height:1.14;color:var(--ink)}
.hero-copy{left:142px;top:392px;width:470px;font-size:11.5px;line-height:1.75;color:var(--text)}

/* about */
.about-bg{left:0;top:640px;width:1200px;height:608px;background:var(--cream)}
.about-frame{left:175px;top:757px;width:366px;height:390px;background:#fff;border-radius:18px;box-shadow:0 6px 22px rgba(0,0,0,.12)}
.about-copy{left:600px;width:458px;font-size:11.5px;line-height:1.78;color:var(--text)}

/* cards */
.card{position:absolute;top:1465px;width:286px;height:358px;background:#fff;border-radius:14px;box-shadow:0 4px 18px rgba(0,0,0,.10)}
.card .photo{left:12px;top:12px;width:262px;height:334px;border-radius:12px}
.card-label{position:absolute;left:12px;width:262px;bottom:30px;text-align:center;color:#fff;font-size:20px;font-weight:600;line-height:1.25}

/* why partner */
.why-bg{left:0;top:2015px;width:1200px;height:605px;background:var(--lilac)}
.ticks{position:absolute;left:140px;top:2198px;list-style:none;font-size:11.3px;color:var(--ink)}
.ticks li{height:28.3px;display:flex;align-items:center;gap:10px}
.ticks svg{width:14px;height:14px}

/* growth */
.growth-copy{left:270px;top:2792px;width:660px;text-align:center;font-size:11.3px;line-height:1.75;color:var(--text)}

/* faq */
.faq-bg{left:0;top:3195px;width:1200px;height:655px;background:var(--mint)}
.faq-item{position:absolute;left:285px;width:628px;background:#fff;border-radius:4px;font-size:12.5px;color:var(--ink);letter-spacing:.3px}
.faq-row{height:44px;display:flex;align-items:center;justify-content:space-between;padding:0 24px}
.faq-row .sign{font-size:18px;font-weight:600}
.faq-open{top:3380px;height:144px;border-bottom:6px solid var(--green)}
.faq-open .faq-row{font-weight:700;border-bottom:1px solid #e8e8e8}
.faq-open p{padding:12px 22px;font-size:11.3px;line-height:1.85;color:var(--text);text-align:justify}

/* contact */
.contact-ghost{left:0;top:3870px;width:1200px;text-align:center;font-size:150px;font-weight:800;letter-spacing:22px;color:#f2f2f2}
.dark-band{left:0;top:4200px;width:1200px;height:270px;background:var(--black)}
.contact-card{left:177px;top:3995px;width:846px;height:348px;background:#fff;box-shadow:0 6px 24px rgba(0,0,0,.10)}
.contact-side{left:670px;top:3995px;width:353px;height:348px;background:var(--cream)}
.field{position:absolute;height:34px;border:1px solid var(--line);font-size:10.5px;color:var(--muted);padding:10px 8px}
.detail{position:absolute;left:705px;display:flex;gap:14px;align-items:flex-start;font-size:11.5px;line-height:1.6;color:var(--ink)}
.ico{width:28px;height:28px;border-radius:50%;border:1px solid var(--orange);display:flex;align-items:center;justify-content:center;flex:none}
.ico svg{width:14px;height:14px}
.social{position:absolute;top:4278px;left:705px;display:flex;gap:22px;font-size:11.5px;color:var(--ink)}
.social span{display:flex;align-items:center;gap:8px}
.social i{width:26px;height:26px;border-radius:50%;border:1px solid var(--orange);display:block}

/* footer */
.foot-nav{position:absolute;top:4397px;left:502px;display:flex;gap:38px;font-size:12px;color:#fff}
.copyright{left:0;top:4483px;width:1200px;text-align:center;font-size:11px;color:var(--text)}
</style>
</head>
<body>

<!-- Header -->
<div class="brand" style="left:146px;top:40px">
  <span class="brand-dot"></span><span class="brand-name">Lantern Petals</span>
</div>
<nav class="nav">
  <span class="active">About Us</span><span>For Supermakets</span><span>For Franchisees</span><span>Contact Us</span>
</nav>

<!-- Hero -->
<h1 class="abs hero-title">Flowers Expressed<br>Feelings Of Surprise,<br>Happiness and gratitude.</h1>
<p class="abs hero-copy">Get franchisor of flower shops. Nibh euismod tincidunt ut laoreet dolore magna aliquam erat volutpat. Ut wisi enim ad minim veniam.</p>
<div class="btn" style="left:140px;top:463px">Get Franchisee</div>

<div class="photo" role="img" aria-label="Two florists arranging a bouquet together in a shop" style="left:648px;top:118px;width:458px;height:458px;border-radius:50%;border:8px solid #fff;box-shadow:0 6px 26px rgba(0,0,0,.12);background:linear-gradient(160deg,#3f78b8 0%,#2f5f98 45%,#c98aa5 80%,#7e4c6a 100%)"></div>
<div class="bloom" role="img" aria-label="Peach blossom flowers" style="left:1020px;top:470px;width:190px;height:290px;border-radius:50% 0 0 50%;background:radial-gradient(circle at 40% 45%,#fdd7c1,#f7a27c 55%,rgba(247,162,124,0) 75%)"></div>
<div class="bloom" role="img" aria-label="Pink daisy flower" style="left:22px;top:575px;width:116px;height:116px;background:radial-gradient(circle,#f6b73c 10%,#e8397b 30%,#f48ab4 60%,rgba(244,138,180,0) 72%)"></div>

<!-- About -->
<div class="abs about-bg"></div>
<div class="abs about-frame"></div>
<div class="photo" role="img" aria-label="Smiling florist surrounded by bright bouquets" style="left:185px;top:765px;width:346px;height:375px;border-radius:12px;background:linear-gradient(170deg,#c9d7a8 0%,#9fb883 40%,#f0c64a 75%,#e8893a 100%)"></div>
<div class="bloom" aria-hidden="true" style="left:393px;top:1058px;width:126px;height:126px;background:#fff;box-shadow:0 3px 12px rgba(0,0,0,.15)"></div>
<div class="bloom" aria-hidden="true" style="left:403px;top:1068px;width:106px;height:106px;background:#e9e3da"></div>
<div class="bloom" role="img" aria-label="Orange roses and greenery" style="left:0;top:990px;width:360px;height:320px;border-radius:45% 55% 50% 40%;background:radial-gradient(ellipse at 40% 55%,#f07a2e 0%,#e65a2c 30%,#6d8f47 55%,rgba(109,143,71,0) 72%)"></div>

<div class="sec-title" style="left:642px;top:742px">About <span class="script">Lantern</span></div>
<p class="abs about-copy" style="top:828px">Fresh flowers convey beauty and love, and in our view should become something every person regularly enjoys. Lantern Petals is an entrepreneurial company created to make top quality fresh flowers and professionally-designed bouquets accessible to every consumer at affordable prices.</p>
<p class="abs about-copy" style="top:930px">Professional florists typically sell the finest quality stems, design the most beautiful bouquets and provide the finest customer service, but their costs – of floral products, retail spaces, labor and marketing – force them to pass high prices along to customers. Supermarket flower departments benefit from high customer footfall, economies of scale and low pricing, but their quality of stems and bouquets is typically poor, staffing is limited, and staff turnover is high which can result in inefficiency, wastage, poorly merchandised selections and limited service.</p>
<div class="btn" style="left:600px;top:1124px">Get Franchisee</div>

<!-- Opportunity -->
<div class="sec-title" style="left:342px;top:1362px">Opportunity For <span class="script">Franchisees</span></div>

<div class="card" style="left:140px"><div class="photo" role="img" aria-label="Woman in a supermarket flower department" style="background:linear-gradient(180deg,#7a9a6c 0%,#4f6e4a 50%,#2d3b27 100%)"></div><div class="card-label">Supermarkets</div></div>
<div class="card" style="left:458px"><div class="photo" role="img" aria-label="Florist arranging flowers in her shop" style="background:linear-gradient(180deg,#b9c3c2 0%,#c9848d 55%,#3a2a2c 100%)"></div><div class="card-label">New Florist<br>Franchisees</div></div>
<div class="card" style="left:776px"><div class="photo" role="img" aria-label="Florist carrying a basket of flowers outside a shop" style="background:linear-gradient(180deg,#8b9aa6 0%,#c4775e 55%,#3b2b27 100%)"></div><div class="card-label">Professional Floral<br>Retailers</div></div>
<div class="btn" style="left:512px;top:1859px">Get Franchisee</div>

<div class="bloom" role="img" aria-label="Mixed bouquet of roses" style="left:1035px;top:1840px;width:175px;height:250px;border-radius:50% 0 0 50%;background:radial-gradient(ellipse at 55% 50%,#f3d34a 0%,#e9446a 35%,#3f7a34 60%,rgba(63,122,52,0) 74%)"></div>
<div class="bloom" role="img" aria-label="Pink daisy flower" style="left:35px;top:1944px;width:90px;height:90px;background:radial-gradient(circle,#f6b73c 10%,#e8397b 30%,#f48ab4 60%,rgba(244,138,180,0) 72%)"></div>

<!-- Why Partner -->
<div class="abs why-bg"></div>
<div class="photo" role="img" aria-label="Florist smelling a large bouquet in a decorated flower shop" style="left:460px;top:2080px;width:740px;height:540px;background:linear-gradient(90deg,rgba(243,243,248,0) 0%,#d9d3d5 25%,#c7a4a8 50%,#9c3a4a 68%,#8d7fa6 85%,#6c7d5c 100%)"></div>
<div class="sec-title" style="left:186px;top:2118px">Why Partner With <span class="script">Lantern</span></div>
<ul class="ticks">
  <li><svg viewBox="0 0 14 14"><rect x="1" y="1" width="12" height="12" rx="2" fill="none" stroke="#f39a1b" stroke-width="1.4"/><path d="M3.5 7l2.5 2.5 5-5" fill="none" stroke="#f39a1b" stroke-width="1.6"/></svg>Low investment and high returns.</li>
  <li><svg viewBox="0 0 14 14"><rect x="1" y="1" width="12" height="12" rx="2" fill="none" stroke="#f39a1b" stroke-width="1.4"/><path d="M3.5 7l2.5 2.5 5-5" fill="none" stroke="#f39a1b" stroke-width="1.6"/></svg>Ready made business in local locality.</li>
  <li><svg viewBox="0 0 14 14"><rect x="1" y="1" width="12" height="12" rx="2" fill="none" stroke="#f39a1b" stroke-width="1.4"/><path d="M3.5 7l2.5 2.5 5-5" fill="none" stroke="#f39a1b" stroke-width="1.6"/></svg>ROI in 12-15 months.</li>
  <li><svg viewBox="0 0 14 14"><rect x="1" y="1" width="12" height="12" rx="2" fill="none" stroke="#f39a1b" stroke-width="1.4"/><path d="M3.5 7l2.5 2.5 5-5" fill="none" stroke="#f39a1b" stroke-width="1.6"/></svg>Delivery throughout the City in less then 2 hours.</li>
  <li><svg viewBox="0 0 14 14"><rect x="1" y="1" width="12" height="12" rx="2" fill="none" stroke="#f39a1b" stroke-width="1.4"/><path d="M3.5 7l2.5 2.5 5-5" fill="none" stroke="#f39a1b" stroke-width="1.6"/></svg>Help in selecting the right location.</li>
  <li><svg viewBox="0 0 14 14"><rect x="1" y="1" width="12" height="12" rx="2" fill="none" stroke="#f39a1b" stroke-width="1.4"/><path d="M3.5 7l2.5 2.5 5-5" fill="none" stroke="#f39a1b" stroke-width="1.6"/></svg>Trained manpower support (Florist).</li>
  <li><svg viewBox="0 0 14 14"><rect x="1" y="1" width="12" height="12" rx="2" fill="none" stroke="#f39a1b" stroke-width="1.4"/><path d="M3.5 7l2.5 2.5 5-5" fill="none" stroke="#f39a1b" stroke-width="1.6"/></svg>Training for franchisee and team.</li>
  <li><svg viewBox="0 0 14 14"><rect x="1" y="1" width="12" height="12" rx="2" fill="none" stroke="#f39a1b" stroke-width="1.4"/><path d="M3.5 7l2.5 2.5 5-5" fill="none" stroke="#f39a1b" stroke-width="1.6"/></svg>Exclusive merchandise and design support.</li>
  <li><svg viewBox="0 0 14 14"><rect x="1" y="1" width="12" height="12" rx="2" fill="none" stroke="#f39a1b" stroke-width="1.4"/><path d="M3.5 7l2.5 2.5 5-5" fill="none" stroke="#f39a1b" stroke-width="1.6"/></svg>Visual merchandising support.</li>
  <li><svg viewBox="0 0 14 14"><rect x="1" y="1" width="12" height="12" rx="2" fill="none" stroke="#f39a1b" stroke-width="1.4"/><path d="M3.5 7l2.5 2.5 5-5" fill="none" stroke="#f39a1b" stroke-width="1.6"/></svg>Quality control team for upkeep of store.</li>
</ul>
<div class="btn" style="left:140px;top:2496px">Get Franchisee</div>

<!-- Our Growth -->
<div class="sec-title" style="left:490px;top:2704px">Our <span class="script">Growth</span></div>
<p class="abs growth-copy">Lorem ipsum dolor sit amet, consectetuer adipiscing elit, sed diam nonummy nibh euismod tincidunt ut laoreet dolore magna aliquam erat volutpat. Ut wisi enim ad minim veniam, quis nostrud exerci tation ullamcorper suscipit lobortis nisl ut aliquip ex ea commodo consequat.</p>

<svg class="abs" style="left:305px;top:2860px" width="590" height="295" viewBox="0 0 590 295" role="img" aria-label="Bar chart of yearly growth from 2018 to 2023">
  <rect x="0" y="0" width="590" height="295" fill="#f7f8f9"/>
  <g stroke="#e3e6ea" stroke-width="1">
    <line x1="0" y1="240" x2="590" y2="240"/><line x1="0" y1="260" x2="590" y2="260"/><line x1="0" y1="280" x2="590" y2="280"/>
  </g>
  <g fill="#1fb13f">
    <rect x="158" y="175" width="22" height="65"/>
    <rect x="203" y="160" width="22" height="80"/>
    <rect x="248" y="140" width="22" height="100"/>
    <rect x="293" y="112" width="22" height="128"/>
    <rect x="338" y="95" width="22" height="145"/>
    <rect x="383" y="66" width="24" height="174"/>
  </g>
  <g fill="#333" font-family="Montserrat,sans-serif" font-size="7" font-weight="600">
    <text x="140" y="173">40%</text><text x="190" y="157">60%</text><text x="238" y="137">70%</text><text x="285" y="109">80%</text><text x="330" y="92">90%</text><text x="375" y="63">100%</text>
  </g>
  <path d="M132 168 L420 30" stroke="#e8431f" stroke-width="6" fill="none"/>
  <path d="M430 24 L404 28 L416 46 Z" fill="#e8431f"/>
  <g fill="#555" font-family="Montserrat,sans-serif" font-size="10" font-weight="600">
    <text x="160" y="262">2018</text><text x="205" y="262">2019</text><text x="250" y="262">2020</text><text x="295" y="262">2021</text><text x="340" y="262">2022</text><text x="385" y="262">2023</text>
  </g>
</svg>

<div class="bloom" role="img" aria-label="Peach blossom flowers" style="left:0;top:3020px;width:170px;height:260px;border-radius:0 50% 50% 0;background:radial-gradient(ellipse at 35% 50%,#fcd6c0,#f59a74 50%,rgba(245,154,116,0) 72%)"></div>
<div class="bloom" role="img" aria-label="Pink daisy flower" style="left:1035px;top:3105px;width:120px;height:120px;background:radial-gradient(circle,#f6b73c 10%,#e8397b 30%,#f48ab4 60%,rgba(244,138,180,0) 72%)"></div>

<!-- FAQ -->
<div class="abs faq-bg"></div>
<div class="sec-title" style="left:336px;top:3276px">Frequently Asked <span class="script">Questions</span></div>

<div class="faq-item faq-open">
  <div class="faq-row"><span>Lorem ipsum dolor sit amet, consectetuer</span><span class="sign">-</span></div>
  <p>Lorem ipsum dolor sit amet, consectetuer adipiscing elit, sed diam nonummy nibh euismod tincidunt ut laoreet dolore magna aliquam erat volutpat. Ut wisi enim ad minim veniam, quis nostrud exerci tation ut aliquip ex ea commodo consequat.</p>
</div>
<div class="faq-item" style="top:3542px"><div class="faq-row"><span>Consectetuer Adipiscing Elit, Sed Diam Nonummy Nibh</span><span class="sign">+</span></div></div>
<div class="faq-item" style="top:3605px"><div class="faq-row"><span>Sed Diam Nonummy &nbsp;Consectetuer Adipiscing Elit</span><span class="sign">+</span></div></div>
<div class="faq-item" style="top:3668px"><div class="faq-row"><span>Consectetuer Adipiscing Elit, Sed Diam Nonummy Nibh</span><span class="sign">+</span></div></div>
<div class="faq-item" style="top:3731px"><div class="faq-row"><span>Sed Diam Nonummy Nibh &nbsp;Consectetuer &nbsp;Elit</span><span class="sign">+</span></div></div>

<div class="bloom" role="img" aria-label="Pastel bouquet of mixed flowers" style="left:945px;top:3640px;width:185px;height:270px;border-radius:50%;background:radial-gradient(ellipse at 50% 45%,#f4b08e 0%,#e96a8a 35%,#8aa36a 58%,rgba(138,163,106,0) 72%)"></div>

<!-- Contact -->
<div class="abs contact-ghost">CONTACT</div>
<div class="abs dark-band"></div>
<div class="abs contact-card"></div>
<div class="abs contact-side"></div>

<h2 class="abs" style="left:352px;top:4028px;font-size:27px;font-weight:700;color:var(--ink)">Contact Us</h2>
<div class="field" style="left:212px;top:4084px;width:204px">Name</div>
<div class="field" style="left:430px;top:4084px;width:205px">Email</div>
<div class="field" style="left:212px;top:4133px;width:204px">Phone No</div>
<div class="field" style="left:430px;top:4133px;width:205px">Subject</div>
<div class="field" style="left:212px;top:4182px;width:423px;height:68px">Message</div>
<div class="btn" style="left:344px;top:4270px">Get Franchisee</div>

<h2 class="abs" style="left:705px;top:4028px;font-size:27px;font-weight:700;color:var(--ink)">Contact Details</h2>
<div class="detail" style="top:4090px"><span class="ico"><svg viewBox="0 0 14 14"><path d="M7 1a4 4 0 0 0-4 4c0 3 4 8 4 8s4-5 4-8a4 4 0 0 0-4-4z" fill="none" stroke="#f39a1b" stroke-width="1.3"/><circle cx="7" cy="5" r="1.4" fill="#f39a1b"/></svg></span><span>123, Lorem Ipsum dolor Lorem Ipsum<br>is dummy text.</span></div>
<div class="detail" style="top:4159px;align-items:center"><span class="ico"><svg viewBox="0 0 14 14"><path d="M3 1.5l2 .3 1 2.7-1.3 1a7 7 0 0 0 3.8 3.8l1-1.3 2.7 1 .3 2c-5 1-10.5-4.5-9.5-9.5z" fill="none" stroke="#f39a1b" stroke-width="1.2"/></svg></span><span>+ 123 456 7890</span></div>
<div class="detail" style="top:4216px;align-items:center"><span class="ico"><svg viewBox="0 0 14 14"><rect x="1.5" y="3" width="11" height="8" fill="none" stroke="#f39a1b" stroke-width="1.2"/><path d="M1.5 3.5L7 8l5.5-4.5" fill="none" stroke="#f39a1b" stroke-width="1.2"/></svg></span><span>hello@petalmail.example</span></div>
<div class="social"><span><i></i>Friendly</span><span><i></i>Chirper</span><span><i></i>Linkwork</span></div>

<!-- Footer -->
<div class="brand" style="left:180px;top:4372px">
  <span class="brand-dot" style="width:40px;height:40px"></span><span class="brand-name" style="font-size:25px">Lantern Petals</span>
</div>
<nav class="foot-nav"><span>Home</span><span>About Us</span><span>For Supermakets</span><span>For Franchisees</span><span>Contact Us</span></nav>
<p class="abs copyright">Copyright 2019 Petalworks Studio. All Rights Reserved</p>

</body>
</html>
```